Emergency and Referral Vet Hospital promotional sticker design

We're looking at getting some stickers designed that we could give to clients to put on their cars for promotion and advertising. If they could also be suitable for a goodie bag for conference too that would be great. I like the look of water-colour backgrounds, we'll need to include our logo and probably our address (Unit 3/215 Korrinup Road Tallowmere). We also have a hospital motto "... because they're family" if that could somehow be integrated, we only care for small animals (dogs, cats etc) but the design is very open to suggestion. Would love to see what you can create.

Industry/Entity Type

Veterinary

Colors
0054AA
0677BA
7BADD7
CADEEF
E8F1F8
0094D4
00A9DD
6FCCEA
C7EBF8
E9F6FB

Requirements
Nice to have
• Think beach vibes, blues maybe paw print shapes etc

```html
<!DOCTYPE html>
<html lang="en">
<head>
<meta charset="utf-8">
<title>Tidewell Vet Hospital – Paw Sticker</title>
<link rel="stylesheet" href="https://fonts.googleapis.com/css2?family=Varela+Round&family=Fira+Sans:ital,wght@1,600&display=swap">
<style>
  :root {
    --backdrop: #cbcbcb;
    --sticker-edge: #ffffff;
    --pad-white: #ffffff;
    --ink-plum: #2e1a2c;
    --wash-light: #c7ebf8;
    --wash-sky: #6fccea;
    --wash-cyan: #00a9dd;
    --wash-mid: #0677ba;
    --wash-deep: #0054aa;
    --wash-navy: #17497a;
  }
  html, body {
    margin: 0;
    padding: 0;
    width: 1200px;
    height: 1200px;
    overflow: hidden;
    background: var(--backdrop);
  }
  .sticker-canvas {
    display: block;
    width: 1200px;
    height: 1200px;
  }
  .sticker-border ellipse {
    fill: var(--sticker-edge);
    stroke: var(--sticker-edge);
    stroke-width: 40px;
  }
  .paw-wash ellipse { fill: url(#watercolour-wash); }
  .wash-glow { fill: url(#wash-glow); }
  .wash-shadow { fill: url(#wash-shadow); }
  .stop-light { stop-color: var(--wash-light); }
  .stop-sky { stop-color: var(--wash-sky); }
  .stop-cyan { stop-color: var(--wash-cyan); }
  .stop-mid { stop-color: var(--wash-mid); }
  .stop-deep { stop-color: var(--wash-deep); }
  .stop-navy { stop-color: var(--wash-navy); }
  .toe-pad, .main-pad { fill: var(--pad-white); }
  .brand-name {
    font-family: "Varela Round", sans-serif;
    font-size: 34px;
    fill: var(--ink-plum);
    letter-spacing: 1px;
  }
  .motto {
    font-family: "Fira Sans", sans-serif;
    font-style: italic;
    font-weight: 600;
    font-size: 19.5px;
    fill: var(--ink-plum);
  }
</style>
</head>
<body>
<svg class="sticker-canvas" viewBox="0 0 1465 1465" xmlns="http://www.w3.org/2000/svg">
  <defs>
    <linearGradient id="watercolour-wash" gradientUnits="userSpaceOnUse" x1="640" y1="470" x2="830" y2="1000">
      <stop offset="0" class="stop-light"/>
      <stop offset="0.2" class="stop-sky"/>
      <stop offset="0.45" class="stop-mid"/>
      <stop offset="0.72" class="stop-deep"/>
      <stop offset="1" class="stop-navy"/>
    </linearGradient>
    <radialGradient id="wash-glow" cx="0.5" cy="0.5" r="0.5">
      <stop offset="0" class="stop-cyan" stop-opacity="0.55"/>
      <stop offset="1" class="stop-cyan" stop-opacity="0"/>
    </radialGradient>
    <radialGradient id="wash-shadow" cx="0.5" cy="0.5" r="0.5">
      <stop offset="0" class="stop-navy" stop-opacity="0.6"/>
      <stop offset="1" class="stop-navy" stop-opacity="0"/>
    </radialGradient>
  </defs>

  <g class="sticker-border">
    <ellipse cx="662" cy="610" rx="108" ry="125"/>
    <ellipse cx="805" cy="600" rx="108" ry="125"/>
    <ellipse cx="555" cy="760" rx="92" ry="120"/>
    <ellipse cx="910" cy="755" rx="92" ry="120"/>
    <ellipse cx="735" cy="830" rx="235" ry="165"/>
    <ellipse cx="735" cy="900" rx="195" ry="95"/>
  </g>

  <g class="paw-wash" role="img" aria-label="Blue and teal watercolour wash texture">
    <ellipse cx="662" cy="610" rx="108" ry="125"/>
    <ellipse cx="805" cy="600" rx="108" ry="125"/>
    <ellipse cx="555" cy="760" rx="92" ry="120"/>
    <ellipse cx="910" cy="755" rx="92" ry="120"/>
    <ellipse cx="735" cy="830" rx="235" ry="165"/>
    <ellipse cx="735" cy="900" rx="195" ry="95"/>
  </g>
  <ellipse class="wash-glow" cx="560" cy="700" rx="90" ry="110"/>
  <ellipse class="wash-shadow" cx="950" cy="790" rx="50" ry="90"/>
  <ellipse class="wash-shadow" cx="790" cy="960" rx="150" ry="35"/>

  <g class="toe-pads">
    <path class="toe-pad" d="M659 528 C700 528 722 580 720 640 C718 680 692 695 660 695 C625 695 598 680 598 640 C598 580 620 528 659 528 Z"/>
    <path class="toe-pad" d="M805 519 C845 519 868 570 868 630 C868 672 842 688 806 688 C770 688 744 672 744 632 C744 572 766 519 805 519 Z"/>
    <path class="toe-pad" d="M555 668 C590 668 605 720 605 770 C605 815 585 832 558 832 C528 832 508 815 508 770 C508 720 522 668 555 668 Z"/>
    <path class="toe-pad" d="M908 662 C940 662 955 712 955 762 C955 805 935 827 905 827 C877 827 857 805 857 762 C857 712 875 662 908 662 Z"/>
  </g>

  <path class="main-pad"
        d="M738 718 C805 714 845 790 875 845 C902 895 885 938 835 938 C795 938 772 924 735 924 C698 924 675 940 635 940 C588 940 566 898 596 846 C628 790 672 722 738 718 Z"/>

  <text class="brand-name" x="738" y="875" text-anchor="middle">tidewell</text>
  <text class="motto" x="731" y="908" text-anchor="middle">“... because they're family"</text>
</svg>
</body>
</html>
```